VocaTerrana Community/ Talent Gallery

VocaTerrana is developing a collaborative career course, with coaching and community exchange. Goal is to offer a platform where talented candidates can show their expertise and find projects, partners, and develop their online portfolios!

Here is a good example of the type of thing we hope to create with focus on sustainability focused talent to task matching
http://www.brambleforth.com/global-themes/employment-and-growth/connecting-talent-with-opportunity-in-the-digital-age

We hope to have a "grid style" gallery where it is easy to search by talent types and focus areas within the scope of "Sustainability" issues...Food/Water/Energy, Public Health, Technology, Sustainable Cities, Infrastructure, Education, Policy, Emerging Economies, Ecosystems, Social Innovation, inclusive Security, Equity Issues. For each topic/ header we hope to have candidates post their completed portfolios to exhibit resumes, biography, a case study... they may actually prepare these on other sites, but can link in OR alternately that they can easily create here, similar to "pinqo.io" ....

Hope to include a blog space titled "Rising over the Rift", where people can mix it up across these topic issues as they are interdependent and often require partners across discipline areas! If possible another area where jobs related to these issues may be posted as project or job opportunities by potential employers.

If there is a way to create a feed from various job sites that already exist...like Jobora...or http://www.greenledgerworks.com/ that would be super great. Again...sort of a portal connection to bridge the gap ....instead of candidates having to search all the time, we are hoping they can advertise their talent and employers may search here for these well presented portfolios!

Target Market(s)

Educators, Students, Career Transitioners, Employers, Professional Associations, Talent Recruiters with focus on Sustainability related Talent to Task matching!

Industry/Entity Type

Sustainability

Number of Pages Required

4 page

Font styles to use
Sans Serif

Colors
3176b5
32b8a4
add136

Requirements
Must have
• Not sure about the coded/ uncoded option here....
• Must have - grid style area where Sustainability Professionals with varied focus areas can exhibit their talent portfolios
• appear as a Talent Gallery that starts with photos & obvious organization...other tabs to be in a menu.
• ability to search both talent and task opportunity areas to help coaches or community members make matches....some topic focused category or tag words to help make them searchable...???
• consistent professional styling to existing website and new artflock postcard shared in brief/ images area
• Interactive blog space where articles, issues may be posted, discussed
• Bulletin board or feed for project opportunities to be posted where candidates may locate them and/or employers may express specific "call" for talent..These may be Short term Internships, Projects, Consulting Team Opportunity, or Jobs/ part time to full time....
Nice to have
• A calendar area where we can post networking opportunities, issues presentations where potential partners can meet the next generation leaders, attend a forum or webinar presentation.
Should not have
• Too much text on front page...Should be clean design,

```html
<!DOCTYPE html>
<html lang="en">
<head>
<meta charset="utf-8">
<title>VocaTerrana – Career Collaboration For A Sustainable Future</title>
<link rel="stylesheet" href="https://fonts.googleapis.com/css2?family=Montserrat:wght@400;600;700&family=Didact+Gothic&family=Lato:wght@400;700&display=swap">
<style>
:root{
  --teal:#32b8a4;
  --teal-deep:#0e7a72;
  --blue:#3176b5;
  --lime:#add136;
  --ink:#1d1d1d;
  --text:#333;
  --muted:#666;
  --navy:#131d2b;
  --line:#3a4656;
  --white:#fff;
}
*{box-sizing:border-box;margin:0;padding:0}
html,body{width:1200px;height:2961px;overflow:hidden}
body{position:relative;background:var(--white);font-family:"Lato",sans-serif;color:var(--text)}
.abs{position:absolute}
.photo{position:absolute;display:block}

/* top bar */
.topbar{left:0;top:0;width:1200px;height:36px;background:var(--teal)}
.social{display:flex;gap:8px;position:absolute}
.social span{width:20px;height:20px;border:1.5px solid rgba(255,255,255,.9);border-radius:2px;display:block}
.topbar .social{left:101px;top:8px}
.phone{left:878px;top:8px;color:#fff;font:400 14px "Montserrat",sans-serif;display:flex;align-items:center;gap:8px}
.login{left:1033px;top:6px;width:70px;height:24px;border:1.5px solid #fff;border-radius:12px;color:#fff;font:700 10px "Montserrat",sans-serif;display:flex;align-items:center;justify-content:center;gap:5px}

/* header */
.header{left:0;top:36px;width:1200px;height:82px;background:#fff}
.brand{left:101px;top:12px;display:flex;align-items:center;gap:12px;font:400 36px "Didact Gothic",sans-serif;color:var(--ink)}
.brand i{width:58px;height:58px;border-radius:50%;background:var(--teal);display:block}
.nav{left:572px;top:22px;display:flex;align-items:center;font:400 15px "Montserrat",sans-serif;color:#222}
.nav a{color:inherit;text-decoration:none;padding:9px 18px}
.nav a+a{margin-left:16px}
.nav .current{background:var(--blue);color:#fff;border-radius:20px;font-weight:600}

/* hero */
.hero{left:0;top:118px;width:1200px;height:474px;background:linear-gradient(180deg,#8a8f7d 0%,#c9a585 40%,#6e5a48 75%,#3a2f27 100%)}
.chev{position:absolute}
.hero-band{left:0;top:510px;width:1200px;height:82px;background:rgba(20,20,20,.62)}
.hero-title{left:118px;top:515px;font:700 29px "Montserrat",sans-serif;color:#fff;letter-spacing:.3px}
.hero-sub{left:118px;top:556px;font:700 18px "Montserrat",sans-serif;color:#fff}
.btn-pill{display:flex;align-items:center;gap:10px;background:var(--teal);color:#fff;border-radius:26px;font:600 15px "Montserrat",sans-serif}
.btn-pill i{display:block;border-radius:50%;background:#fff}
.learn{left:868px;top:526px;width:174px;height:50px;padding-left:4px}
.learn i{width:42px;height:42px}

/* welcome */
.welcome-title{left:101px;top:626px;font:400 34px "Didact Gothic",sans-serif;color:var(--ink)}
.welcome-title b{font:700 34px "Montserrat",sans-serif}
.welcome-copy{left:101px;top:694px;width:548px;font-size:14px;line-height:24px;color:var(--text)}
.welcome-list{left:101px;top:772px;width:540px;list-style:none;font-size:14px;line-height:26.5px}
.welcome-list li{padding-left:22px;position:relative}
.welcome-list li::before{content:"";position:absolute;left:4px;top:11px;width:6px;height:6px;border-radius:50%;background:#222}
.read{left:101px;top:928px;width:144px;height:40px;padding-left:3px;font-size:14px}
.read i{width:34px;height:34px}

.phase-panel{left:0;top:592px;width:1200px;height:427px;background:var(--teal-deep);clip-path:polygon(746px 0,1200px 0,1200px 427px,632px 427px)}
.phase-title{left:750px;top:628px;font:400 31px "Didact Gothic",sans-serif;color:#fff;line-height:38px}
.phase-title b{font:700 31px "Montserrat",sans-serif}
.phase{position:absolute;left:734px;display:flex;align-items:center;gap:20px}
.phase .ring{width:58px;height:58px;border-radius:50%;background:#fff;display:flex;align-items:center;justify-content:center}
.phase .core{width:46px;height:46px;border-radius:50%;background:#1c2630;display:flex;align-items:center;justify-content:center}
.phase h4{font:700 15px "Montserrat",sans-serif;letter-spacing:3.5px;color:#fff}
.phase p{font:400 11px "Lato",sans-serif;color:var(--lime);margin-top:3px;line-height:14px}

/* services */
.forest{left:0;top:1019px;width:632px;height:471px;background:linear-gradient(180deg,#6a8a4a 0%,#a8c07c 45%,#e8ecd6 70%,#5c7a3c 100%);clip-path:polygon(0 0,632px 0,517px 471px,0 471px)}
.services-title{left:880px;top:1080px;width:222px;text-align:right;font:400 33px "Didact Gothic",sans-serif;color:var(--ink)}
.services-title b{font:700 33px "Montserrat",sans-serif}
.rule{position:absolute;height:2px;background:var(--teal)}
.services-box{left:71px;top:1155px;width:1060px;height:270px;background:#fff;box-shadow:0 2px 10px rgba(0,0,0,.25)}
.card{position:absolute;overflow:hidden}
.card .cap{position:absolute;left:0;bottom:0;width:100%;height:30px;background:rgba(30,30,30,.6);color:#fff;font:600 17px "Montserrat",sans-serif;display:flex;align-items:center;padding-left:10px}
.card .cap.center{justify-content:center;padding-left:0}

/* gallery */
.section-title{position:absolute;left:0;width:1200px;text-align:center;font:400 32px "Didact Gothic",sans-serif;color:var(--ink)}
.section-title b{font:700 32px "Montserrat",sans-serif}

/* blog */
.post{position:absolute;width:312px}
.post .img{position:relative;width:312px;height:150px;border:1px solid #ddd}
.post .date{position:absolute;left:6px;top:-2px;width:34px;height:44px;background:var(--blue);color:#fff;text-align:center;font:700 17px "Montserrat",sans-serif;line-height:18px;padding-top:4px;clip-path:polygon(0 0,100% 0,100% 100%,50% 84%,0 100%)}
.post .date small{display:block;font-size:10px;line-height:12px}
.post h3{font:700 14px "Lato",sans-serif;color:#111;margin-top:17px}
.post p{font-size:11.5px;line-height:16px;color:#444;margin-top:6px}
.post a{display:block;margin-top:10px;font:700 13px "Lato",sans-serif;color:var(--teal);text-decoration:none}

/* footer */
.footer{left:0;top:2420px;width:1200px;height:541px;background:var(--navy)}
.foot-nav{position:absolute;top:2470px;font:400 17px "Montserrat",sans-serif;color:#d8dde3;transform:translateX(-50%)}
.foot-rule{left:101px;top:2517px;width:1001px;height:1px;background:var(--line)}
.foot-head{position:absolute;top:2556px;font:700 18px "Montserrat",sans-serif;color:#fff}
.field{position:absolute;left:101px;width:319px;border:1px solid #5c6776;color:#d8dde3;font:400 12px "Lato",sans-serif;padding:8px 10px}
.submit{left:101px;top:2829px;width:127px;height:38px;background:var(--teal);color:#fff;font:700 16px "Montserrat",sans-serif;display:flex;align-items:center;justify-content:center;letter-spacing:.5px}
.foot-emblem{left:509px;top:2621px;width:206px;height:206px;border-radius:50%;background:#8d9196;display:flex;align-items:center;justify-content:center;font:700 22px "Montserrat",sans-serif;color:#fff}
.map{left:830px;top:2590px;width:300px;height:220px;background:radial-gradient(ellipse at center,rgba(255,255,255,.07),rgba(255,255,255,0) 70%)}
.contact{position:absolute;left:806px;display:flex;gap:14px}
.contact .ico{width:30px;height:30px;border-radius:50%;border:1.5px solid #9aa3ad;display:flex;align-items:center;justify-content:center;flex:none}
.contact h5{font:700 13px "Lato",sans-serif;color:#fff}
.contact p{font:400 12px "Lato",sans-serif;color:#c9ced5;line-height:17px}
.follow{left:806px;top:2818px;font:400 13px "Lato",sans-serif;color:#c9ced5}
.footer-social{left:806px;top:2842px}
.footer-social span{border:none;width:22px;height:22px}
.copy{left:0;top:2925px;width:1200px;text-align:center;font:400 12px "Lato",sans-serif;color:#c9ced5}
</style>
</head>
<body>

<!-- top bar -->
<div class="abs topbar">
  <div class="social"><span></span><span></span><span></span><span></span></div>
  <div class="abs phone">
    <svg width="16" height="16" viewBox="0 0 24 24" fill="#fff"><path d="M6.6 10.8a15.1 15.1 0 0 0 6.6 6.6l2.2-2.2c.3-.3.7-.4 1-.2 1.1.4 2.3.6 3.6.6.6 0 1 .4 1 1V20c0 .6-.4 1-1 1A17 17 0 0 1 3 4c0-.6.4-1 1-1h3.5c.6 0 1 .4 1 1 0 1.3.2 2.5.6 3.6.1.3 0 .7-.2 1z"/></svg>
    012.345.6789
  </div>
  <div class="abs login">
    <svg width="9" height="11" viewBox="0 0 9 11" fill="#fff"><rect x="0" y="4.5" width="9" height="6.5" rx="1"/><path d="M2 4.5V3a2.5 2.5 0 0 1 5 0v1.5" stroke="#fff" stroke-width="1.3" fill="none"/></svg>
    LOGIN
  </div>
</div>

<!-- header -->
<div class="abs header">
  <div class="abs brand"><i></i>VocaTerrana</div>
  <nav class="abs nav">
    <a class="current">HOME</a><a>ABOUT</a><a>SERVICES</a><a>BLOG</a><a>CONTACT</a>
  </nav>
</div>

<!-- hero -->
<div class="photo hero" role="img" aria-label="Cupped hands of several people holding soil with a young green seedling"></div>
<svg class="chev" style="left:36px;top:310px" width="24" height="90" viewBox="0 0 24 90"><path d="M22 2 2 45l20 43" stroke="#fff" stroke-width="1.5" fill="none" opacity=".8"/></svg>
<svg class="chev" style="left:1140px;top:310px" width="24" height="90" viewBox="0 0 24 90"><path d="m2 2 20 43-20 43" stroke="#fff" stroke-width="1.5" fill="none" opacity=".8"/></svg>
<div class="abs hero-band"></div>
<div class="abs hero-title">Career Collaboration For A Sustainable Future</div>
<div class="abs hero-sub">Course, Coaching, Community</div>
<div class="abs btn-pill learn"><i></i>Learn More</div>

<!-- welcome -->
<h1 class="abs welcome-title"><b>Welcome to</b> VocaTerrana</h1>
<p class="abs welcome-copy">Lorem ipsum dolor sit amet, consectetur adipiscing elit. Sed vitae magna tellus. Aenean ante nunc, semper nec cursus non, rutrum ac eros. Vestibulum mattis justo ac dui bibendum consequat a ac ipsum.</p>
<ul class="abs welcome-list">
  <li>Lorem ipsum dolor sit amet, consectetur adipiscing elit</li>
  <li>Lorem ipsum dolor sit amet, consectetu</li>
  <li>Lorem ipsum dolor sit amet, consectetur adipiscing</li>
  <li>Lorem ipsum dolor sit amet, consectetur adip</li>
  <li>Lorem ipsum dolor sit amet, consectetur adipis</li>
</ul>
<div class="abs btn-pill read"><i></i>Read More</div>

<div class="abs phase-panel"></div>
<h2 class="abs phase-title"><b>Four Phase</b><br>Career Course</h2>

<div class="phase" style="top:724px">
  <div class="ring"><div class="core"><svg width="26" height="16" viewBox="0 0 26 16"><path d="M1 8C5 2 9 1 13 1s8 1 12 7c-4 6-8 7-12 7S5 14 1 8z" fill="#fff"/><circle cx="13" cy="8" r="4" fill="#1c2630"/><circle cx="13" cy="8" r="1.6" fill="#fff"/></svg></div></div>
  <div><h4>CLARIFY</h4><p>Personal Profile, Vision &amp; Mission</p></div>
</div>
<div class="phase" style="top:790px">
  <div class="ring"><div class="core"><svg width="22" height="18" viewBox="0 0 22 18" fill="#fff"><path d="M1 8h7v9H1zM1 8c0-4 2-7 6-7v3c-2 0-3 2-3 4zM13 8h7v9h-7zM13 8c0-4 2-7 6-7v3c-2 0-3 2-3 4z"/></svg></div></div>
  <div><h4>COMMUNICATE</h4><p>Strengths &amp; Strategies for Positive Change</p></div>
</div>
<div class="phase" style="top:856px">
  <div class="ring"><div class="core"><svg width="24" height="22" viewBox="0 0 24 22" fill="#fff"><path d="M2 2h15a1 1 0 0 1 1 1v9a1 1 0 0 1-1 1H8l-4 4v-4H2a1 1 0 0 1-1-1V3a1 1 0 0 1 1-1z"/><path d="M19 7h3v9h-2v3l-3-3h-7v-2h8a1 1 0 0 0 1-1z" opacity=".8"/></svg></div></div>
  <div><h4>COLLABORATE</h4><p>Proactive Projects, Proving Performance Results!</p></div>
</div>
<div class="phase" style="top:922px">
  <div class="ring"><div class="core"><svg width="24" height="24" viewBox="0 0 24 24" fill="none" stroke="#fff" stroke-width="1.6"><circle cx="12" cy="12" r="10"/><ellipse cx="12" cy="12" rx="4.5" ry="10"/><path d="M2 12h20M4 6.5h16M4 17.5h16"/></svg></div></div>
  <div><h4>CREATE</h4><p>Creating Change &amp; Innovation for Sustainable<br>Future(s)!</p></div>
</div>

<!-- services -->
<div class="photo forest" role="img" aria-label="Looking up at tall forest trees and green canopy"></div>
<h2 class="abs services-title"><b>Our</b> Services</h2>
<div class="rule" style="left:895px;top:1130px;width:207px"></div>
<div class="abs services-box"></div>
<div class="card" style="left:101px;top:1188px;width:237px;height:206px">
  <div class="photo" style="inset:0;background:linear-gradient(160deg,#f4f6ef 0%,#b9d88a 45%,#6f9a3a 70%,#d9b79a 100%)" role="img" aria-label="Hands passing a small green plant"></div>
  <div class="cap">Next Generation Talent</div>
</div>
<div class="card" style="left:355px;top:1188px;width:237px;height:206px">
  <div class="photo" style="inset:0;background:linear-gradient(160deg,#e7e9ec 0%,#a9b6c4 45%,#6f7f94 75%,#c4b09c 100%)" role="img" aria-label="Colleagues working together around a laptop"></div>
  <div class="cap center">Our Courses</div>
</div>
<div class="card" style="left:610px;top:1188px;width:237px;height:206px">
  <div class="photo" style="inset:0;background:linear-gradient(160deg,#f1efe9 0%,#d6d2c8 45%,#7f8b98 75%,#bfb6a8 100%)" role="img" aria-label="Person at a desk joining an online coaching session"></div>
  <div class="cap center">Online Coaching</div>
</div>
<div class="card" style="left:864px;top:1188px;width:238px;height:206px">
  <div class="photo" style="inset:0;background:linear-gradient(160deg,#7a9a5e 0%,#8e8470 45%,#5e6e86 75%,#9a8a74 100%)" role="img" aria-label="Large group gathered outdoors for an in-person session"></div>
  <div class="cap center">In-person Coaching</div>
</div>

<!-- gallery -->
<h2 class="section-title" style="top:1544px"><b>View</b> Gallery</h2>
<div class="rule" style="left:496px;top:1592px;width:208px"></div>
<svg class="chev" style="left:34px;top:1750px" width="24" height="90" viewBox="0 0 24 90"><path d="M22 2 2 45l20 43" stroke="#bbb" stroke-width="1.5" fill="none"/></svg>
<svg class="chev" style="left:1142px;top:1750px" width="24" height="90" viewBox="0 0 24 90"><path d="m2 2 20 43-20 43" stroke="#bbb" stroke-width="1.5" fill="none"/></svg>

<div class="card" style="left:101px;top:1636px;width:316px;height:162px">
  <div class="photo" style="inset:0;background:linear-gradient(180deg,#cfe0ee 0%,#9fb9cf 35%,#6d9a6a 65%,#4e7a5a 100%)" role="img" aria-label="Aerial view of a green modern city by the water"></div>
  <div class="cap center">Infrastructure</div>
</div>
<div class="card" style="left:436px;top:1636px;width:154px;height:162px">
  <div class="photo" style="inset:0;background:linear-gradient(180deg,#eef0f2 0%,#cfd4da 50%,#9a8a7a 100%)" role="img" aria-label="Teacher presenting to a classroom"></div>
  <div class="cap center">Education</div>
</div>
<div class="card" style="left:610px;top:1636px;width:154px;height:162px">
  <div class="photo" style="inset:0;background:linear-gradient(180deg,#4d6b2e 0%,#7fa04a 45%,#c69c7c 100%)" role="img" aria-label="Many hands holding young plants"></div>
  <div class="cap center">Community</div>
</div>
<div class="card" style="left:786px;top:1636px;width:316px;height:162px">
  <div class="photo" style="inset:0;background:linear-gradient(180deg,#c9ccd0 0%,#6f7d8c 40%,#6c8f4a 75%,#4c6a34 100%)" role="img" aria-label="Student among solar panels on a green roof"></div>
  <div class="cap center">Education</div>
</div>

<div class="card" style="left:101px;top:1814px;width:154px;height:162px">
  <div class="photo" style="inset:0;background:linear-gradient(180deg,#bfe2f2 0%,#d8b08f 40%,#6fa23e 75%,#4d7a2c 100%)" role="img" aria-label="Hands forming a heart around a tree"></div>
  <div class="cap center">Ecosystems</div>
</div>
<div class="card" style="left:274px;top:1814px;width:316px;height:162px">
  <div class="photo" style="inset:0;background:linear-gradient(180deg,#f0b24a 0%,#e08a2c 50%,#3a2a1c 100%)" role="img" aria-label="Construction workers silhouetted against a sunset"></div>
  <div class="cap center">Infrastructure</div>
</div>
<div class="card" style="left:610px;top:1814px;width:316px;height:162px">
  <div class="photo" style="inset:0;background:linear-gradient(160deg,#0d2f6a 0%,#1f63b0 45%,#5fa6e0 75%,#9ab6cc 100%)" role="img" aria-label="Hand touching a glowing digital technology interface"></div>
  <div class="cap center">Technology</div>
</div>
<div class="card" style="left:948px;top:1814px;width:154px;height:162px">
  <div class="photo" style="inset:0;background:linear-gradient(180deg,#e8eef4 0%,#cfe0c2 45%,#7fb04a 75%,#b8c6d4 100%)" role="img" aria-label="Seedling growing in a laboratory dish"></div>
  <div class="cap center">Ecosystems</div>
</div>

<!-- blog -->
<h2 class="section-title" style="top:2030px;font-size:30px"><b style="font-size:30px">Rising</b> Over The Rift</h2>
<div class="rule" style="left:488px;top:2076px;width:224px"></div>
<svg class="chev" style="left:40px;top:2166px" width="20" height="26" viewBox="0 0 20 26"><circle cx="10" cy="13" r="10" fill="#f1f1f1"/><path d="m12 7-6 6 6 6" stroke="#222" stroke-width="2" fill="none"/></svg>
<svg class="chev" style="left:1140px;top:2166px" width="20" height="26" viewBox="0 0 20 26"><circle cx="10" cy="13" r="10" fill="#f1f1f1"/><path d="m8 7 6 6-6 6" stroke="#222" stroke-width="2" fill="none"/></svg>

<article class="post" style="left:101px;top:2104px">
  <div class="img"><div class="photo" style="inset:0;background:linear-gradient(150deg,#f2ece2 0%,#d9cdb8 45%,#2a64b8 70%,#c9a48a 100%)" role="img" aria-label="Hand placing a blue puzzle piece marked Coach among career words"></div><div class="date">23<small>JUN</small></div></div>
  <h3>Sed ut perspiciatis unde iste mo</h3>
  <p>Duis autem vel eum iriure dolor in hendrerit ink vulput ate velit esse molestie facilisis.</p>
  <a>Read More »</a>
</article>
<article class="post" style="left:444px;top:2104px">
  <div class="img"><div class="photo" style="inset:0;background:linear-gradient(180deg,#2f8a3a 0%,#3d77b0 35%,#c49478 70%,#a67858 100%)" role="img" aria-label="Two hands sharing a small globe of the earth"></div><div class="date">23<small>JUN</small></div></div>
  <h3>Sed ut perspiciatis unde iste mo</h3>
  <p>Duis autem vel eum iriure dolor in hendrerit ink vulput ate velit esse molestie facilisis.</p>
  <a>Read More »</a>
</article>
<article class="post" style="left:786px;top:2104px">
  <div class="img"><div class="photo" style="inset:0;background:linear-gradient(180deg,#f4f1ee 0%,#e0bca4 45%,#c48a6a 100%)" role="img" aria-label="Many hands stacked together in teamwork"></div><div class="date">23<small>JUN</small></div></div>
  <h3>Sed ut perspiciatis unde iste mo</h3>
  <p>Duis autem vel eum iriure dolor in hendrerit ink vulput ate velit esse molestie facilisis.</p>
  <a>Read More »</a>
</article>

<!-- footer -->
<footer class="abs footer"></footer>
<span class="foot-nav" style="left:270px">HOME</span>
<span class="foot-nav" style="left:422px">ABOUT</span>
<span class="foot-nav" style="left:590px">SERVICES</span>
<span class="foot-nav" style="left:750px">BLOG</span>
<span class="foot-nav" style="left:910px">CONTACT</span>
<div class="abs foot-rule"></div>

<h3 class="foot-head" style="left:103px">QUICK INQUIRY</h3>
<div class="field" style="top:2610px;height:34px">Name</div>
<div class="field" style="top:2655px;height:34px">Email</div>
<div class="field" style="top:2702px;height:34px">Phone</div>
<div class="field" style="top:2748px;height:70px">Message</div>
<div class="abs submit">SUBMIT</div>

<div class="abs foot-emblem">VocaTerrana</div>

<div class="photo map" role="img" aria-label="Faint world map behind the contact details"></div>
<h3 class="foot-head" style="left:806px">CONTACT DETAILS</h3>
<div class="contact" style="top:2608px">
  <div class="ico"><svg width="12" height="16" viewBox="0 0 12 16" fill="#fff"><path d="M6 0a6 6 0 0 1 6 6c0 4.5-6 10-6 10S0 10.5 0 6a6 6 0 0 1 6-6z"/><circle cx="6" cy="6" r="2.2" fill="#131d2b"/></svg></div>
  <div><h5>VocaTerrana</h5><p>213, Lorem Street, Mapple Road,<br>Opp Ipsum Street, Sky View, CA - 123456</p></div>
</div>
<div class="contact" style="top:2692px">
  <div class="ico"><svg width="14" height="10" viewBox="0 0 14 10" fill="none" stroke="#fff" stroke-width="1.4"><rect x=".7" y=".7" width="12.6" height="8.6"/><path d="m.7.7 6.3 5 6.3-5"/></svg></div>
  <div><h5>EMAIL</h5><p>info@vocaterrana.com</p></div>
</div>
<div class="contact" style="top:2752px">
  <div class="ico"><svg width="13" height="13" viewBox="0 0 24 24" fill="#fff"><path d="M6.6 10.8a15.1 15.1 0 0 0 6.6 6.6l2.2-2.2c.3-.3.7-.4 1-.2 1.1.4 2.3.6 3.6.6.6 0 1 .4 1 1V20c0 .6-.4 1-1 1A17 17 0 0 1 3 4c0-.6.4-1 1-1h3.5c.6 0 1 .4 1 1 0 1.3.2 2.5.6 3.6.1.3 0 .7-.2 1z"/></svg></div>
  <div><h5>CALL US</h5><p>012.345.6789</p></div>
</div>
<div class="abs follow">Follow Us:</div>
<div class="abs social footer-social">
  <span style="background:var(--blue)"></span><span style="background:var(--blue)"></span><span style="background:var(--teal)"></span><span style="background:#c9473a"></span>
</div>

<div class="abs copy">Copyright © 2016 VocaTerrana.  All Rights Reserved.</div>

</body>
</html>
```